Business Card Design - Amberfield Court

We are looking at a new design for our business cards that has a modern and professional look. We run a residential aged care facility focussing on the care of residents. The cards will be used for potential clients, consultants and business opportunities in this sector. Blue and white is our main colours and would to see these colours incorporated in the design.
Industry/Entity Type
Business
Contact Information for Business Card
Amberfield Court, Darren Walsh, dwalsh@amberfieldcourt.com.au, Finance Manager, 0472 639 208, BCom, 37 Marrabel Crescent, Brindle Vale, Qld 4093.
Look and feel
Each slider illustrates characteristics of the customer's brand and the style your logo design should communicate.

```html
<!DOCTYPE html>
<html lang="en">
<head>
<meta charset="utf-8">
<title>Amberfield Court – Business Card</title>
<link rel="stylesheet" href="https://fonts.googleapis.com/css2?family=Open+Sans:wght@400;600&display=swap">
<style>
  :root {
    --backdrop: #e9e6e3;
    --card: #0d0d0f;
    --brand-blue: #5d8cab;
    --text-light: #e4e6e8;
    --text-muted: #8e9398;
    --divider: #55595e;
    --icon: #a9aeb3;
  }
  * { margin: 0; padding: 0; box-sizing: border-box; }
  html, body {
    width: 1200px; height: 814px; overflow: hidden;
    background: var(--backdrop);
    font-family: "Open Sans", Arial, sans-serif;
  }
  .sheet {
    position: relative; width: 1200px; height: 814px;
    display: flex; align-items: center; justify-content: center; gap: 50px;
  }
  .card {
    position: relative; width: 540px; height: 310px;
    background: var(--card);
    box-shadow: 0 10px 24px rgba(0,0,0,.25);
  }
  /* contact side */
  .brand-mark {
    position: absolute; left: 34px; top: 0; bottom: 0; width: 220px;
    display: flex; align-items: center; gap: 12px;
  }
  .brand-dot {
    width: 22px; height: 22px; border-radius: 50%; background: var(--brand-blue); flex: none;
  }
  .brand-name {
    color: var(--brand-blue); font-size: 25px; font-weight: 600; line-height: 1.1;
  }
  .divider {
    position: absolute; left: 262px; top: 62px; width: 1px; height: 180px;
    background: var(--divider);
  }
  .details { position: absolute; left: 282px; top: 64px; color: var(--text-light); }
  .person { color: var(--brand-blue); font-size: 19px; font-weight: 600; }
  .person .credential { font-size: 13px; font-weight: 400; }
  .role { color: var(--text-muted); font-size: 13px; margin-bottom: 12px; }
  .address { font-size: 13.5px; line-height: 1.4; margin-bottom: 10px; }
  .contact-line { display: flex; align-items: center; gap: 8px; font-size: 13.5px; line-height: 1.55; }
  .contact-line svg { width: 12px; height: 12px; flex: none; }
  /* logo side */
  .card-back { display: flex; align-items: center; justify-content: center; gap: 14px; }
  .card-back .brand-dot { width: 26px; height: 26px; background: var(--text-light); }
  .card-back .brand-name { color: var(--text-light); font-size: 34px; }
</style>
</head>
<body>
<main class="sheet">
  <section class="card card-front">
    <div class="brand-mark">
      <span class="brand-dot"></span>
      <span class="brand-name">Amberfield Court</span>
    </div>
    <div class="divider"></div>
    <div class="details">
      <p class="person">Darren Walsh <span class="credential">BCom</span></p>
      <p class="role">Finance Manager</p>
      <p class="address">37 Marrabel Crescent<br>Brindle Vale, Qld 4093.</p>
      <p class="contact-line">
        <svg viewBox="0 0 12 12" aria-hidden="true"><path fill="var(--icon)" d="M2.5 0.5l2 2.3-1 1.4c.7 1.5 1.8 2.6 3.3 3.3l1.4-1 2.3 2-1.2 2C5 10.5 1.5 7 .5 1.7z"/></svg>
        0472 639 208
      </p>
      <p class="contact-line">
        <svg viewBox="0 0 12 12" aria-hidden="true"><rect x="0.5" y="2" width="11" height="8" rx="1" fill="var(--icon)"/><path d="M1 2.6l5 3.8 5-3.8" stroke="var(--card)" stroke-width="1" fill="none"/></svg>
        dwalsh@amberfieldcourt.com.au
      </p>
      <p class="contact-line">
        <svg viewBox="0 0 12 12" aria-hidden="true"><circle cx="6" cy="6" r="5.3" fill="none" stroke="var(--icon)" stroke-width="1.2"/><ellipse cx="6" cy="6" rx="2.2" ry="5.3" fill="none" stroke="var(--icon)" stroke-width="1"/><path d="M.8 6h10.4" stroke="var(--icon)" stroke-width="1"/></svg>
        www.amberfieldcourt.com.au
      </p>
    </div>
  </section>
  <section class="card card-back">
    <span class="brand-dot"></span>
    <span class="brand-name">Amberfield Court</span>
  </section>
</main>
</body>
</html>
```